Design and Renovation Company Luxury Business Card

I want to create a luxury business card for a Design and Renovation Firm . We will use our current logo. The company name is 528BUILDA. We do not want anything standard. We need a very unique concept.
Please see uploaded inspiration. I really like the textured paper option. I would like the card to be thick with debossing, and/or embossing options. The logo has orange in it but I would like to see the card with and without the orange. I think the orange may make the company feel less high-end. The goal is to elevate the logo not match its vibe per se of the logo. We want something very unique, not standard at all!
I would like a space for :
Logo,
Name,
Position,
Email,
Office number,
Website Address,
Business Address,
Thank you!
Have fun!
Target Market(s)
Home owners Age 35 +
Industry/Entity Type
Design and Renovation
Contact Information for Business Card
Logo, Name, Position, Email, Office number, Website Address, Business Address,.
Colors
Designer to choose colors to be used in the design.
Requirements
Must have
- A luxury designer feel. Must be black or dark grey but open to other luxury ideas.
Nice to have
- Gold, silver, black embossing or debossing. Textured paper design.
Should not have
- A cheap look and feel.

```html
<!DOCTYPE html>
<html lang="en">
<head>
<meta charset="utf-8">
<title>528BUILDA Business Card</title>
<link href="https://fonts.googleapis.com/css2?family=Open+Sans:wght@400;700&display=swap" rel="stylesheet">
<style>
  :root {
    --page-bg: #d2d6d5;
    --card-bg: #232428;
    --card-rim: #ffffff;
    --text-light: #ffffff;
    --mark-ink: #141517;
    --line-dark: #111214;
    --icon-bg: #1a1b1e;
    --tile-light: #e9e9e9;
    --tile-mid: #6a6b6e;
    --tile-dark: #141416;
  }
  * { margin: 0; padding: 0; box-sizing: border-box; }
  html, body { width: 1200px; height: 960px; overflow: hidden; }
  body {
    background: var(--page-bg);
    font-family: "Open Sans", Arial, sans-serif;
    position: relative;
  }
  .card {
    position: absolute;
    top: 105px;
    width: 428px;
    height: 749px;
    border-radius: 30px;
    border: 4px solid var(--card-rim);
    overflow: hidden;
    box-shadow: 0 14px 26px rgba(0,0,0,0.35);
  }
  .card-back { left: 144px; }
  .card-front { left: 632px; background: var(--card-bg); }

  .tile-pattern {
    width: 100%;
    height: 100%;
    background:
      radial-gradient(ellipse 90% 55% at 0% 0%, var(--tile-light) 0%, rgba(120,120,122,0.7) 40%, transparent 75%),
      linear-gradient(170deg, var(--tile-mid) 0%, #2a2b2e 45%, var(--tile-dark) 100%);
  }

  .brand {
    position: absolute;
    left: 0; right: 0;
    top: 168px;
    display: flex;
    justify-content: center;
    align-items: center;
    gap: 14px;
  }
  .brand-square {
    width: 34px;
    height: 34px;
    background: var(--mark-ink);
  }
  .brand-name {
    font-weight: 700;
    font-size: 38px;
    line-height: 1;
    letter-spacing: 1px;
    color: var(--text-light);
    white-space: nowrap;
  }

  .person {
    position: absolute;
    left: 0; right: 0;
    top: 372px;
    text-align: center;
    color: var(--text-light);
  }
  .person-name { font-weight: 700; font-size: 27px; line-height: 1.15; }
  .person-role { font-size: 19px; line-height: 1.2; }

  .connectors { position: absolute; left: 0; top: 0; width: 420px; height: 741px; }

  .contact-list {
    position: absolute;
    left: 0; right: 0;
    top: 492px;
    text-align: center;
    list-style: none;
    color: var(--text-light);
    font-size: 19px;
    line-height: 25.5px;
  }
  .address {
    position: absolute;
    left: 58px;
    top: 643px;
    width: 312px;
    height: 71px;
    border: 3px solid var(--line-dark);
    display: flex;
    flex-direction: column;
    justify-content: center;
    text-align: center;
    font-style: normal;
    font-size: 18px;
    line-height: 24px;
    color: var(--text-light);
  }
</style>
</head>
<body>
  <section class="card card-back">
    <div class="tile-pattern" role="img" aria-label="Mosaic of small square tiles fading from silver at the top left to black"></div>
  </section>

  <section class="card card-front">
    <div class="brand">
      <span class="brand-square"></span>
      <span class="brand-name">528BUILDA</span>
    </div>

    <div class="person">
      <p class="person-name">Radek Voláček</p>
      <p class="person-role">Director</p>
    </div>

    <svg class="connectors" viewBox="0 0 420 741" aria-hidden="true">
      <g fill="none" stroke="var(--line-dark)" stroke-width="3">
        <polyline points="148,455 67,455 67,534 80,534"/>
        <polyline points="279,455 363,455 363,557 345,557"/>
        <line x1="213" y1="470" x2="213" y2="482"/>
        <line x1="213" y1="625" x2="213" y2="637"/>
      </g>
      <g fill="var(--line-dark)">
        <polygon points="80,527 90,534 80,541"/>
        <polygon points="345,550 335,557 345,564"/>
        <polygon points="206,482 220,482 213,490"/>
        <polygon points="206,637 220,637 213,645"/>
      </g>
      <g fill="var(--icon-bg)">
        <circle cx="163" cy="455" r="15"/>
        <circle cx="213" cy="455" r="15"/>
        <circle cx="264" cy="455" r="15"/>
        <circle cx="213" cy="610" r="15"/>
      </g>
      <g fill="none" stroke="#ffffff" stroke-width="1.5" stroke-linejoin="round">
        <rect x="155" y="450" width="16" height="11"/>
        <polyline points="155,450 163,457 171,450"/>
        <path d="M208,448 l3,0 l2,4 l-2,2 q2,4 6,6 l2,-2 l4,2 l0,3 q-10,1 -15,-15 z"/>
        <circle cx="264" cy="455" r="7"/>
        <line x1="257" y1="455" x2="271" y2="455"/>
        <ellipse cx="264" cy="455" rx="3" ry="7"/>
        <path d="M213,619 q-6,-6 -6,-11 a6,6 0 0 1 12,0 q0,5 -6,11 z"/>
        <circle cx="213" cy="608" r="2"/>
      </g>
    </svg>

    <ul class="contact-list">
      <li>+001 555 218 0394</li>
      <li>info@yourwebsite.com</li>
      <li>www.yourwebsite.com</li>
    </ul>

    <address class="address">
      <span>1180 Harlow Works Avenue •</span>
      <span>Brookfield, CO 80611</span>
    </address>
  </section>
</body>
</html>
```